Telecommunications/Power civil contractor needs business card design

Were a new telecommunications/power underground civil contractor that is looking for a new business card design. Our company colours are silver or grey and orange. Feel free to use the white background logo or the black background logo.

Target Market(s)

Local contractors, utility companies, private sector mining/energy companies, developers.

Industry/Entity Type

Telecommunications

Contact Information for Business Card

Each card will need the following info:
Persons name:
Title:
E-mail:
Phone number:
Shop Address:
Mailing Address:

Requirements
Must have
• Each card will need the following info:
• Persons name:
• Title:
• E-mail:
• Phone number:
• Shop Address:
• Mailing Address:

```html
<!DOCTYPE html>
<html lang="en">
<head>
<meta charset="utf-8">
<title>Delta Duct Contracting Inc — Business Card</title>
<link rel="stylesheet" href="https://fonts.googleapis.com/css2?family=Michroma&family=Roboto:ital,wght@0,400;1,400&display=swap">
<style>
  :root {
    --page: #e4e2df;
    --card-grey: #676767;
    --card-light: #ededed;
    --silver: #c9c9c9;
    --silver-dark: #9a9a9a;
    --orange: #f26522;
    --ink-dark: #2b2b2b;
    --ink-mid: #3a3a3a;
  }
  * { margin: 0; padding: 0; box-sizing: border-box; }
  html, body { width: 1200px; height: 864px; overflow: hidden; }
  body {
    background: var(--page);
    display: flex;
    flex-direction: column;
    align-items: center;
    justify-content: center;
    gap: 40px;
    font-family: "Roboto", Arial, sans-serif;
  }
  .card {
    position: relative;
    width: 640px;
    height: 366px;
    overflow: hidden;
    box-shadow: 0 6px 18px rgba(0,0,0,0.18);
  }

  /* Front side */
  .card--front {
    background: var(--card-grey);
    display: flex;
    flex-direction: column;
    align-items: center;
    justify-content: center;
    gap: 26px;
  }
  .brand-dot {
    width: 92px;
    height: 92px;
    border-radius: 50%;
    border: 7px solid var(--silver);
  }
  .brand-name {
    font-family: "Michroma", Arial, sans-serif;
    color: var(--silver);
    text-align: center;
    line-height: 1.25;
    letter-spacing: 1px;
  }
  .card--front .brand-name { font-size: 34px; }
  .brand-name span { display: block; font-size: 0.52em; letter-spacing: 2px; }

  /* Back side */
  .card--back { background: var(--card-light); }
  .card-backdrop { position: absolute; inset: 0; }
  .contact {
    position: absolute;
    left: 56px;
    top: 46px;
    color: var(--ink-dark);
  }
  .contact__name { font-size: 26px; font-weight: 400; }
  .contact__title { font-size: 17px; font-style: italic; margin-top: 2px; }
  .contact__address { font-size: 15px; line-height: 1.3; margin-top: 36px; }
  .contact__lines { list-style: none; margin-top: 22px; font-size: 15px; }
  .contact__lines li { display: flex; align-items: center; gap: 10px; height: 22px; }
  .icon { width: 14px; height: 14px; flex: none; }
  .card--back .brand {
    position: absolute;
    right: 40px;
    top: 118px;
    width: 240px;
    display: flex;
    flex-direction: column;
    align-items: center;
    gap: 20px;
  }
  .card--back .brand-dot { width: 70px; height: 70px; border: 6px solid var(--silver-dark); }
  .card--back .brand-name { color: var(--orange); font-size: 24px; }
</style>
</head>
<body>

  <section class="card card--front" aria-label="Card front">
    <div class="brand-dot"></div>
    <p class="brand-name">DELTA DUCT<span>CONTRACTING INC</span></p>
  </section>

  <section class="card card--back" aria-label="Card back">
    <svg class="card-backdrop" viewBox="0 0 640 366" preserveAspectRatio="none" aria-hidden="true">
      <path d="M0 0 H416 C360 110 320 230 300 366 H0 Z" fill="#c9c9c9"/>
      <path d="M0 0 H404 C350 110 310 230 290 366 H0 Z" fill="#676767"/>
    </svg>

    <div class="contact">
      <h1 class="contact__name">Alex Morgan</h1>
      <p class="contact__title">General Manager</p>
      <p class="contact__address">Street Address,&nbsp; Suite 00<br>Statename 00000</p>
      <ul class="contact__lines">
        <li>
          <svg class="icon" viewBox="0 0 14 14"><rect width="14" height="14" rx="2" fill="#2b2b2b"/><rect x="4.5" y="2" width="5" height="10" rx="1" fill="none" stroke="#9a9a9a" stroke-width="1.2"/></svg>
          555 0142 7788
        </li>
        <li>
          <svg class="icon" viewBox="0 0 14 14"><rect width="14" height="14" rx="2" fill="#2b2b2b"/><path d="M4 3 L6 5 L5 6.5 Q6.5 8.5 8 9 L9 8 L11 10 L9.5 11.5 Q4.5 10 2.5 4.5 Z" fill="#9a9a9a"/></svg>
          555 0199 3120
        </li>
        <li>
          <svg class="icon" viewBox="0 0 14 14"><rect width="14" height="14" rx="2" fill="#2b2b2b"/><rect x="2.5" y="4" width="9" height="6" fill="none" stroke="#9a9a9a" stroke-width="1.2"/><path d="M2.5 4 L7 7.5 L11.5 4" fill="none" stroke="#9a9a9a" stroke-width="1.2"/></svg>
          info@deltaductworks.com
        </li>
        <li>
          <svg class="icon" viewBox="0 0 14 14"><rect width="14" height="14" rx="2" fill="#2b2b2b"/><circle cx="7" cy="7" r="4.5" fill="none" stroke="#9a9a9a" stroke-width="1.1"/><path d="M2.5 7 H11.5 M7 2.5 V11.5" stroke="#9a9a9a" stroke-width="1"/></svg>
          www.deltaductworks.com
        </li>
      </ul>
    </div>

    <div class="brand">
      <div class="brand-dot"></div>
      <p class="brand-name">DELTA DUCT<span>CONTRACTING INC</span></p>
    </div>
  </section>

</body>
</html>
```